Business Cards Design for the electrical wholesaler: clean bold dynamic :)

We need a business card design that would follow our latest brand guidelines. As an electrical wholesaler we want to bring a fresh look and feel into the industry. The design should be clean bold and dynamic. It should come alive with the renewed energy of our green colour. Our grey colour should keep things balanced and complement the notion of maturity and responsibility. We employ Lato as a corporate font however are not bound by this font and we’re open to interpretation here.

Target Market(s)

Electrical contractors

Industry/Entity Type

Business

Contact Information for Business Card

Logo
Name & Surname: Halyna Dorosh
Job Title: Director of Marketing
Email: halya.dorosh@quillmail.example
Cell phone: 780.555.0126
Address: 20517 - 87 Ave. Edmonton, AB, Canada. T6K 4N8
Business Phone: 780.555.0184
Website: www.brovix.example

Font styles to use
Other font styles liked:
• Lato

Requirements
Must have
• Logo & website
Nice to have
• Brand elements - some of them you may find in the attached Brand Guidelines (e.g. three lines on the background signifying "W")

```html
<!DOCTYPE html>
<html lang="en">
<head>
<meta charset="utf-8">
<title>brovix — Business Card</title>
<link rel="stylesheet" href="https://fonts.googleapis.com/css2?family=Oswald:wght@600&family=Work+Sans:wght@400;500;600&display=swap">
<style>
  :root {
    --backdrop: #161716;
    --backdrop-edge: #0c0c0c;
    --card: #2a2c2a;
    --card-shade: #232523;
    --green: #7dc242;
    --white: #f4f5f2;
  }
  * { box-sizing: border-box; margin: 0; padding: 0; }
  html, body { width: 1200px; height: 900px; overflow: hidden; }
  body {
    background: radial-gradient(ellipse at 50% 40%, var(--backdrop) 0%, var(--backdrop-edge) 100%);
    font-family: "Work Sans", sans-serif;
    color: var(--white);
    display: flex;
    flex-direction: column;
    align-items: center;
    justify-content: center;
    gap: 40px;
  }
  .card {
    width: 630px;
    height: 360px;
    background: linear-gradient(135deg, var(--card) 0%, var(--card-shade) 100%);
    box-shadow: 0 18px 40px rgba(0,0,0,.55);
    position: relative;
  }

  /* Front */
  .card--front { display: flex; align-items: center; justify-content: center; }
  .brand { display: flex; flex-direction: column; align-items: flex-end; }
  .brand__row { display: flex; align-items: center; gap: 16px; }
  .brand__square { width: 42px; height: 42px; background: var(--green); }
  .brand__name {
    font-weight: 500;
    font-size: 76px;
    line-height: 1;
    letter-spacing: 1px;
    color: var(--white);
  }
  .brand__tagline {
    margin-top: 6px;
    font-size: 11px;
    font-weight: 600;
    letter-spacing: 3px;
    text-transform: uppercase;
  }

  /* Back */
  .card--back { padding: 92px 28px 0 40px; }
  .contact-block { display: flex; align-items: center; }
  .person { text-align: right; padding-right: 20px; white-space: nowrap; }
  .person__name {
    font-family: "Oswald", sans-serif;
    font-weight: 600;
    font-size: 36px;
    line-height: 1;
    letter-spacing: 1px;
    color: var(--green);
    text-transform: uppercase;
  }
  .person__title { margin-top: 8px; font-size: 14px; letter-spacing: 1px; }
  .divider { width: 2px; height: 96px; background: var(--green); flex: none; }
  .details { list-style: none; padding-left: 18px; white-space: nowrap; }
  .details li {
    display: flex; align-items: center; gap: 10px;
    font-size: 13.5px; letter-spacing: .5px; line-height: 24px;
  }
  .details svg { width: 12px; height: 12px; flex: none; }
  .details .accent { color: var(--green); }
  .address {
    position: absolute; left: 40px; bottom: 44px;
    font-size: 15px; letter-spacing: 1.5px; white-space: nowrap;
  }
</style>
</head>
<body>
  <section class="card card--front" aria-label="Card front">
    <div class="brand">
      <div class="brand__row">
        <span class="brand__square" aria-hidden="true"></span>
        <span class="brand__name">brovix</span>
      </div>
      <span class="brand__tagline">Electrical Wholesalers</span>
    </div>
  </section>

  <section class="card card--back" aria-label="Card back">
    <div class="contact-block">
      <div class="person">
        <p class="person__name">Halyna Dorosh</p>
        <p class="person__title">Director of Marketing</p>
      </div>
      <span class="divider" aria-hidden="true"></span>
      <ul class="details">
        <li>
          <svg viewBox="0 0 12 12" aria-hidden="true"><path d="M2.5 1 L4.5 1 L5.2 3.6 L4 4.6 Q5 7 7.4 8 L8.4 6.8 L11 7.5 L11 9.5 Q11 11 9.5 11 Q1 10.5 1 2.5 Q1 1 2.5 1Z" fill="var(--green)"/></svg>
          780.555.0184
        </li>
        <li>
          <svg viewBox="0 0 12 12" aria-hidden="true"><rect x="3" y="0.8" width="6" height="10.4" rx="1" fill="none" stroke="var(--green)" stroke-width="1.2"/><circle cx="6" cy="9.2" r=".7" fill="var(--green)"/></svg>
          780.555.0126
        </li>
        <li>
          <svg viewBox="0 0 12 12" aria-hidden="true"><rect x="1" y="2.5" width="10" height="7" fill="none" stroke="var(--green)" stroke-width="1.2"/><path d="M1 2.5 L6 6.5 L11 2.5" fill="none" stroke="var(--green)" stroke-width="1.2"/></svg>
          halya.dorosh@quillmail.example
        </li>
        <li>
          <svg viewBox="0 0 12 12" aria-hidden="true"><circle cx="6" cy="6" r="5" fill="none" stroke="var(--green)" stroke-width="1.1"/><ellipse cx="6" cy="6" rx="2.2" ry="5" fill="none" stroke="var(--green)" stroke-width="1"/><path d="M1 6 H11" stroke="var(--green)" stroke-width="1"/></svg>
          <span>www.<span class="accent">brovix</span>.example</span>
        </li>
      </ul>
    </div>
    <p class="address">20517 - 87 Ave. Edmonton, AB, Canada. T6K 4N8</p>
  </section>
</body>
</html>
```